Business Card for a Creative Technology based HR services company

Our company name is Lumo8, and we build large communities of HR (human resource) and finance personnels through our mobile platform, and we conduct lots of on-line and off-line activities to get everyone constantly connected. Behind all these, we will also provide on-site HR and finance contractors to our clients, plus a host of other HR-related services. No process in our company takes more than 5-steps.
Our company slogan: Touching Your Future
Target Market(s)
All human resource (HR) and finance personnels, from new entrants to highly experienced senior professionals.
Industry/Entity Type
Finance
Colors
Designer to choose colors to be used in the design.
Look and feel
Each slider illustrates characteristics of the customer's brand and the style your logo design should communicate.

```html
<!DOCTYPE html>
<html lang="en">
<head>
<meta charset="utf-8">
<title>Lumo8 Business Card</title>
<link rel="stylesheet" href="https://fonts.googleapis.com/css2?family=Open+Sans:wght@400;600;700&family=Oswald:wght@400;500&display=swap">
<style>
  :root {
    --navy: #0f2a55;
    --red: #ee1c24;
    --white: #ffffff;
    --paper-1: #eef1f5;
    --paper-2: #dde3ec;
    --paper-3: #c9d2df;
    --charcoal: #3a3a3c;
    --backdrop: #e9e6e1;
    --shadow: rgba(0, 0, 0, 0.18);
  }
  * { box-sizing: border-box; margin: 0; padding: 0; }
  html, body { width: 1076px; height: 1200px; overflow: hidden; }
  body {
    background: var(--backdrop);
    position: relative;
    font-family: "Open Sans", Arial, sans-serif;
  }
  .card {
    position: absolute;
    left: 108px;
    width: 860px;
    height: 492px;
    background: var(--white);
    box-shadow: 0 12px 30px var(--shadow);
    overflow: hidden;
  }
  .card--front { top: 64px; }
  .card--back { top: 644px; }

  /* Front */
  .front-frame {
    position: absolute;
    inset: 22px;
    background: var(--red);
  }
  .front-field {
    position: absolute;
    inset: 36px;
    background: var(--navy);
  }
  .paper-stack {
    position: absolute;
    left: 240px;
    top: 160px;
    width: 380px;
    height: 150px;
  }
  .paper {
    position: absolute;
    width: 380px;
    height: 150px;
    box-shadow: 0 2px 4px rgba(0,0,0,0.15);
  }
  .paper--3 { left: 0; top: 24px; background: var(--paper-3); }
  .paper--2 { left: 4px; top: 16px; background: var(--paper-2); }
  .paper--1 { left: 8px; top: 8px; background: var(--paper-1); }
  .paper--top {
    left: 12px; top: 0;
    background: var(--white);
    display: flex;
    align-items: center;
    justify-content: center;
  }
  .brand-name {
    font-family: "Open Sans", Arial, sans-serif;
    font-weight: 700;
    color: var(--navy);
    letter-spacing: -1px;
    line-height: 1;
  }
  .paper--top .brand-name { font-size: 64px; }

  /* Back */
  .card--back .brand-name {
    position: absolute;
    left: 120px;
    top: 150px;
    font-size: 92px;
  }
  .name-band {
    position: absolute;
    left: 310px;
    top: 354px;
    width: 380px;
    bottom: 0;
    background: var(--navy);
    padding: 28px 0 0 34px;
    color: var(--white);
  }
  .person-name {
    font-family: "Oswald", "Arial Narrow", sans-serif;
    font-weight: 500;
    font-size: 40px;
    letter-spacing: 1px;
    line-height: 1;
  }
  .person-role {
    font-family: "Oswald", "Arial Narrow", sans-serif;
    font-weight: 400;
    font-size: 16px;
    letter-spacing: 3px;
    margin-top: 10px;
  }
  .contact-panel {
    position: absolute;
    left: 498px;
    top: 188px;
    width: 292px;
    height: 166px;
    background: var(--red);
    padding: 20px 20px 0 0;
    color: var(--white);
    font-size: 13px;
    line-height: 1.35;
  }
  .contact-row {
    display: flex;
    flex-direction: column;
    align-items: flex-end;
    height: 46px;
  }
  .side-strip {
    position: absolute;
    left: 790px;
    top: 188px;
    right: 0;
    bottom: 0;
    background: var(--charcoal);
    padding-top: 22px;
    display: flex;
    flex-direction: column;
    align-items: center;
    gap: 14px;
  }
  .contact-icon {
    width: 32px;
    height: 32px;
    border-radius: 50%;
    background: var(--white);
    display: flex;
    align-items: center;
    justify-content: center;
  }
  .contact-icon svg { width: 18px; height: 18px; fill: var(--charcoal); }
</style>
</head>
<body>
  <section class="card card--front" aria-label="Card front">
    <div class="front-frame"></div>
    <div class="front-field">
      <div class="paper-stack">
        <div class="paper paper--3"></div>
        <div class="paper paper--2"></div>
        <div class="paper paper--1"></div>
        <div class="paper paper--top"><span class="brand-name">Lumo8</span></div>
      </div>
    </div>
  </section>

  <section class="card card--back" aria-label="Card back">
    <span class="brand-name">Lumo8</span>

    <div class="contact-panel">
      <div class="contact-row"><span>555 210 4477</span><span>555 210 4478</span></div>
      <div class="contact-row"><span>hello@lumo8.com</span><span>www.lumo8.com</span></div>
      <div class="contact-row"><span>120 Harbor Street</span><span>Leeds, LS1 4AB</span></div>
    </div>

    <div class="side-strip">
      <span class="contact-icon" aria-label="Phone">
        <svg viewBox="0 0 24 24"><path d="M6.6 10.8a15.1 15.1 0 0 0 6.6 6.6l2.2-2.2a1 1 0 0 1 1-.25 11.4 11.4 0 0 0 3.6.57 1 1 0 0 1 1 1V20a1 1 0 0 1-1 1A17 17 0 0 1 3 4a1 1 0 0 1 1-1h3.5a1 1 0 0 1 1 1c0 1.25.2 2.45.57 3.57a1 1 0 0 1-.25 1z"/></svg>
      </span>
      <span class="contact-icon" aria-label="Web">
        <svg viewBox="0 0 24 24"><path d="M12 2a10 10 0 1 0 0 20 10 10 0 0 0 0-20zm6.9 6h-3a15.6 15.6 0 0 0-1.4-3.6A8 8 0 0 1 18.9 8zM12 4a14 14 0 0 1 1.9 4h-3.8A14 14 0 0 1 12 4zM4.3 14a8.2 8.2 0 0 1 0-4h3.4a16.5 16.5 0 0 0 0 4zm.8 2h3a15.6 15.6 0 0 0 1.4 3.6A8 8 0 0 1 5.1 16zm3-8h-3a8 8 0 0 1 4.4-3.6A15.6 15.6 0 0 0 8.1 8zM12 20a14 14 0 0 1-1.9-4h3.8A14 14 0 0 1 12 20zm2.3-6H9.7a14.7 14.7 0 0 1 0-4h4.6a14.7 14.7 0 0 1 0 4zm.2 5.6a15.6 15.6 0 0 0 1.4-3.6h3a8 8 0 0 1-4.4 3.6zm1.8-5.6a16.5 16.5 0 0 0 0-4h3.4a8.2 8.2 0 0 1 0 4z"/></svg>
      </span>
      <span class="contact-icon" aria-label="Address">
        <svg viewBox="0 0 24 24"><path d="M12 2a7 7 0 0 0-7 7c0 5.25 7 13 7 13s7-7.75 7-13a7 7 0 0 0-7-7zm0 9.5A2.5 2.5 0 1 1 12 6.5a2.5 2.5 0 0 1 0 5z"/></svg>
      </span>
    </div>

    <div class="name-band">
      <div class="person-name">DANA WHITFIELD</div>
      <div class="person-role">GENERAL MANAGER</div>
    </div>
  </section>
</body>
</html>
```